Fizz's Shed & Grill Burger Restaurant Website - HomePage Only PSD

I need a website design for a restaurant called "Fizz's Shed and Grill" featuring burgers, wings, beer, live music, trivia, and more. I have several images of the restaurant and they already have their logo files created (see attached). I want some type of wood background and integrate the silver tin. This needs to be a modern, hip and fun type design. Design must incorporate these attached graphics.

UPDATE - just added a few more images of things I really like to be incorporated into my designs.
Updates

Industry/Entity Type

Burger Restaurant

Number of Pages Required

1 page

Font styles to use
Sans Serif

Requirements
Must have
• Restaurant/Bar theme with integration of existing logo and the red wood look.
Nice to have
• - Modern Fun appearance
• - Use Pelko Fonts

```html
<!DOCTYPE html>
<html lang="en">
<head>
<meta charset="utf-8">
<title>Fizz's Shed and Grill</title>
<link href="https://fonts.googleapis.com/css2?family=Cabin+Sketch:wght@400;700&family=Lato:wght@400;700&family=Raleway:wght@600;700&display=swap" rel="stylesheet">
<style>
:root{
  --topbar:#2a1a0c;
  --wood-light:#c99a62;
  --wood-mid:#b07a44;
  --wood-dark:#8a5a2e;
  --brown-deep:#3d2710;
  --brown-band:#452c12;
  --accent:#c08a4a;
  --accent-text:#c7873f;
  --cream:#f2e6d4;
  --white:#ffffff;
  --ink:#333333;
  --night:#1a1411;
  --footer-ink:#2b1a0a;
}
*{box-sizing:border-box;margin:0;padding:0}
html,body{width:1200px;height:2736px;overflow:hidden}
body{position:relative;font-family:'Lato',sans-serif;color:var(--ink);background:var(--brown-deep)}
.wood{background:
  repeating-linear-gradient(90deg,rgba(90,50,20,.06) 0 3px,transparent 3px 23px,rgba(255,230,190,.05) 23px 27px,transparent 27px 61px),
  linear-gradient(90deg,var(--wood-mid),var(--wood-light) 30%,var(--wood-mid) 55%,var(--wood-light) 80%,var(--wood-mid))}
.abs{position:absolute}
.script{font-family:'Cabin Sketch',sans-serif;letter-spacing:2px}
.btn{display:inline-block;background:var(--accent);color:var(--white);font-family:'Raleway',sans-serif;font-weight:700;font-size:16px;padding:8px 16px}

/* top bar */
.topbar{left:0;top:0;width:1200px;height:51px;background:var(--topbar);color:var(--cream);font-size:14px}
.topbar .contact{position:absolute;left:100px;top:17px;display:flex;gap:36px;align-items:center}
.topbar .contact span{display:flex;align-items:center;gap:8px}
.topbar .social{position:absolute;right:100px;top:12px;display:flex;gap:12px}
.topbar .social i{width:28px;height:28px;border:1.5px solid var(--accent);border-radius:50%;display:block}

/* header */
.header{left:0;top:51px;width:1200px;height:109px}
.nav{position:absolute;right:100px;top:50px;display:flex;gap:52px;font-family:'Cabin Sketch',sans-serif;font-size:17px;color:var(--white);letter-spacing:1px}
.nav .active{color:var(--footer-ink)}
.badge{position:absolute;left:100px;top:51px;width:200px;height:137px;z-index:5}
.badge .name{position:absolute;left:0;top:20px;width:200px;text-align:center;font-family:'Cabin Sketch',sans-serif;font-weight:700;font-size:24px;line-height:1.1;color:var(--footer-ink)}

/* hero */
.hero{left:0;top:160px;width:1200px;height:511px;background:linear-gradient(180deg,#8fb4d6 0%,#b9c9d3 35%,#8a8a7a 60%,#6f6650 100%)}
.hero .caption{position:absolute;left:405px;top:216px;width:398px;height:68px;background:rgba(40,40,40,.55);color:var(--white);font-family:'Raleway',sans-serif;font-weight:700;font-size:34px;text-align:center;line-height:68px}
.hero .arrow{position:absolute;top:218px;width:40px;height:36px;background:rgba(30,30,30,.8)}
.features{left:0;top:671px;width:1200px;height:334px}
.card{position:absolute;top:606px;width:310px;height:355px;background:var(--white);box-shadow:0 4px 10px rgba(0,0,0,.35);padding:9px;text-align:center}
.card .photo{height:165px}
.card h3{font-family:'Raleway',sans-serif;font-weight:600;color:var(--accent-text);font-size:21px;margin:16px 0 10px;letter-spacing:1px}
.card p{font-size:13.5px;line-height:20px;padding:0 6px;color:#222}
.card .btn{margin-top:16px;font-size:15px;padding:7px 15px}

/* welcome */
.welcome{left:0;top:1005px;width:1200px;height:399px;background:var(--brown-band);color:var(--cream)}
.heading{position:absolute;left:0;width:1200px;text-align:center;font-size:33px;color:var(--white)}
.divider{position:absolute;left:300px;width:600px;height:2px;background:rgba(200,160,110,.4)}
.seal{position:absolute;width:36px;height:36px;border-radius:50%;background:var(--cream);border:2px solid var(--brown-deep)}
.welcome .lead{position:absolute;left:100px;top:135px;font-size:19px;color:var(--white)}
.welcome .body{position:absolute;left:100px;top:172px;width:548px;font-size:13.5px;line-height:27px}
.welcome .btn{position:absolute;left:100px;top:323px}
.welcome .photo{position:absolute;left:690px;top:127px;width:412px;height:232px;border:2px solid var(--cream);background:linear-gradient(160deg,#8db3da,#b8a58c 45%,#6b5a45)}

/* gallery */
.gallery{left:0;top:1404px;width:1200px;height:571px}
.gallery .heading{color:var(--footer-ink)}
.tile{position:absolute;box-shadow:0 2px 6px rgba(0,0,0,.35)}
.tile::after{content:"";position:absolute;inset:12px;border:1px solid rgba(255,255,255,.55)}

/* testimonials & booking */
.reviews{left:0;top:1975px;width:1200px;height:456px;background:radial-gradient(ellipse at 40% 50%,#3a2e26,#14100d 75%);color:var(--white)}
.reviews .title{position:absolute;font-size:33px;color:var(--white)}
.rule{position:absolute;height:1px;background:rgba(255,255,255,.3)}
.avatar{position:absolute;left:330px;top:144px;width:132px;height:132px;border-radius:50%;border:4px solid var(--white);background:linear-gradient(180deg,#c9b8a4,#7a6a5a)}
.quote{position:absolute;left:180px;top:295px;width:440px;text-align:center;font-size:14px;line-height:27px;color:#ddd}
.quote b{color:#888;font-size:30px;font-family:Georgia,serif;line-height:0;vertical-align:-8px}
.author{position:absolute;left:180px;top:390px;width:440px;text-align:center;font-family:'Raleway',sans-serif;font-weight:700;font-size:16px}
.vline{position:absolute;left:684px;top:95px;height:320px;border-left:2px dashed rgba(255,255,255,.3)}
.field{position:absolute;left:756px;width:346px;height:38px;border:1px solid rgba(255,255,255,.55);display:flex;align-items:center;font-size:14px;font-family:'Raleway',sans-serif;font-weight:600}
.field svg{margin:0 18px 0 12px}
.submit{position:absolute;left:756px;top:380px;background:var(--accent);color:var(--white);font-family:'Raleway',sans-serif;font-weight:700;font-size:15px;padding:7px 30px}

/* footer */
.footer{left:0;top:2431px;width:1200px;height:252px;color:var(--white)}
.footer h4{font-family:'Cabin Sketch',sans-serif;font-size:14px;font-weight:400;letter-spacing:1px;margin-bottom:12px}
.col{position:absolute;top:40px;font-size:13.5px;line-height:23px}
.col ul{list-style:none}
.col li::before{content:"›";margin-right:10px}
.col strong{font-weight:700}
.map{width:180px;height:124px;background:linear-gradient(135deg,#d8e6c8,#aac9e2 50%,#e9e3d3);border:1px solid #eee}
.follow li{list-style:none;display:flex;align-items:center;gap:10px;margin-bottom:8px;font-size:11px;font-weight:700;letter-spacing:.5px}
.follow li::before{content:none}
.follow i{display:block;width:26px;height:26px;border-radius:50%;background:var(--white)}
.footer-mark{position:absolute;left:928px;top:40px;width:174px;height:174px;border-radius:50%;border:3px solid var(--white);display:flex;align-items:center;justify-content:center;text-align:center;font-family:'Cabin Sketch',sans-serif;font-weight:700;font-size:24px;line-height:1.15}
.copyright{left:0;top:2683px;width:1200px;height:53px;background:var(--night);color:var(--white);text-align:center;line-height:53px;font-size:13px;font-weight:700}
</style>
</head>
<body>

<div class="abs topbar">
  <div class="contact">
    <span><svg width="14" height="14" viewBox="0 0 24 24" fill="#c08a4a"><path d="M6.6 10.8a15 15 0 006.6 6.6l2.2-2.2c.3-.3.7-.4 1-.2 1.1.4 2.3.6 3.6.6.6 0 1 .4 1 1V20c0 .6-.4 1-1 1A17 17 0 013 4c0-.6.4-1 1-1h3.5c.6 0 1 .4 1 1 0 1.3.2 2.5.6 3.6.1.3 0 .7-.2 1z"/></svg>123-456-789</span>
    <span><svg width="16" height="12" viewBox="0 0 16 12" fill="#c08a4a"><rect width="16" height="12" rx="1"/><path d="M1 1l7 5 7-5" stroke="#2a1a0c" stroke-width="1.4" fill="none"/></svg>info@fizzsshed.com</span>
  </div>
  <div class="social"><i></i><i></i><i></i><i></i></div>
</div>

<div class="abs header wood">
  <nav class="nav"><span class="active">HOME</span><span>RESTAURANT</span><span>BAR</span><span>EVENTS</span><span>GALLERY</span><span>CONTACT US</span></nav>
</div>
<div class="badge">
  <svg width="200" height="137" viewBox="0 0 200 137" style="position:absolute;left:0;top:0"><path d="M0 0h200v112L100 137 0 112z" fill="#fff"/></svg>
  <div class="name">Fizz's Shed<br>and Grill</div>
</div>

<div class="abs hero" role="img" aria-label="Photo of a painted cow statue outside the restaurant entrance">
  <div class="caption">Best Burger In Town</div>
  <div class="arrow" style="left:0"><svg width="40" height="36"><path d="M23 11l-7 7 7 7" stroke="#fff" stroke-width="3" fill="none"/></svg></div>
  <div class="arrow" style="right:0"><svg width="40" height="36"><path d="M17 11l7 7-7 7" stroke="#fff" stroke-width="3" fill="none"/></svg></div>
</div>
<div class="abs features wood"></div>

<div class="card" style="left:98px">
  <div class="photo" role="img" aria-label="Photo of a stacked burger" style="background:linear-gradient(180deg,#b01010,#c48a3a 50%,#6a3a12)"></div>
  <h3>FOOD</h3>
  <p>Lorem ipsum dolor sit amet, consectetur adipiscing elit, sed do eiusmod tempor incididunt ut labore et dolore magna aliqua. Ut enim</p>
  <span class="btn">Read More</span>
</div>
<div class="card" style="left:445px">
  <div class="photo" role="img" aria-label="Photo of a red cocktail at the bar" style="background:linear-gradient(180deg,#2a1a14,#7a2020 60%,#1a1010)"></div>
  <h3>DRINK</h3>
  <p>Lorem ipsum dolor sit amet, consectetur adipiscing elit, sed do eiusmod tempor incididunt ut labore et dolore magna aliqua. Ut enim</p>
  <span class="btn">Read More</span>
</div>
<div class="card" style="left:792px">
  <div class="photo" role="img" aria-label="Photo of a guitarist playing live music" style="background:linear-gradient(135deg,#3a1a30,#b03a2a 50%,#1a1a3a)"></div>
  <h3>MUSIC</h3>
  <p>Lorem ipsum dolor sit amet, consectetur adipiscing elit, sed do eiusmod tempor incididunt ut labore et dolore magna aliqua. Ut enim</p>
  <span class="btn">Read More</span>
</div>

<section class="abs welcome">
  <h2 class="heading script" style="top:32px">WELCOME TO FIZZ'S SHED AND GRILL</h2>
  <div class="divider" style="top:97px"></div>
  <div class="seal" style="left:582px;top:80px"></div>
  <p class="lead">Lorem ipsum dolor sit amet, consectetur adipiscing elit.</p>
  <p class="body">Sed ut perspiciatis unde omnis iste natus error sit voluptatem accusantium doloremque laudantium, totam rem aperiam, eaque ipsa quae ab illo inventore veritatis et quasi architecto beatae vitae dicta sunt explicabo. Nemo enim ipsam voluptatem quia voluptas sit aspernatur aut odit aut fugit, sed quia consequuntur magni dolores eos qui ratione voluptatem sequi nesciunt.</p>
  <span class="btn">Read More</span>
  <div class="photo" role="img" aria-label="Photo of the restaurant's wooden porch and patio"></div>
</section>

<section class="abs gallery wood">
  <h2 class="heading script" style="top:38px">PHOTO GALLERY</h2>
  <div class="seal" style="left:582px;top:88px;width:34px;height:34px;background:transparent;border-color:var(--footer-ink)"></div>
  <div class="tile" style="left:98px;top:159px;width:370px;height:367px;background:linear-gradient(135deg,#6a4a30,#9a2a2a 40%,#d8d0c8 60%,#2a3a6a)" role="img" aria-label="Photo of a painted flag on a barn wall inside"></div>
  <div class="tile" style="left:476px;top:159px;width:376px;height:188px;background:linear-gradient(180deg,#8a6a4a,#6a4a30)" role="img" aria-label="Photo of a tin sign above a lounge seat"></div>
  <div class="tile" style="left:476px;top:352px;width:181px;height:174px;background:linear-gradient(135deg,#d04040,#e0a040 50%,#3a2a2a)" role="img" aria-label="Photo of a drink on the bar"></div>
  <div class="tile" style="left:666px;top:352px;width:186px;height:174px;background:linear-gradient(180deg,#6a5040,#9a8a7a)" role="img" aria-label="Photo of a wall sign on wood paneling"></div>
  <div class="tile" style="left:861px;top:159px;width:241px;height:367px;background:linear-gradient(180deg,#3a2a1a,#6a4a30 50%,#2a2018)" role="img" aria-label="Photo of the interior with string lights"></div>
</section>

<section class="abs reviews">
  <h2 class="title script" style="left:100px;top:40px">HAPPY CUSTOMERS</h2>
  <div class="rule" style="left:100px;top:100px;width:518px"></div>
  <div class="seal" style="left:100px;top:84px;width:32px;height:32px;border-color:#555"></div>
  <svg class="abs" style="left:555px;top:70px" width="48" height="22"><circle cx="10" cy="11" r="8" fill="none" stroke="#ccc" stroke-width="1.5"/><path d="M12 7l-4 4 4 4" stroke="#ccc" stroke-width="1.5" fill="none"/><circle cx="34" cy="11" r="8" fill="none" stroke="#ccc" stroke-width="1.5"/><path d="M32 7l4 4-4 4" stroke="#ccc" stroke-width="1.5" fill="none"/></svg>
  <div class="avatar" role="img" aria-label="Customer portrait"></div>
  <p class="quote"><b>“</b> Duis autem vel eum iriure dolor in hendrerit in vulputate velitj esse molestie consequat, vel illum dolore eu feugiat nulla facilis sis at vero eros et accumsan et delenit facilisi. <b>”</b></p>
  <p class="author">Mr. Dale Marrow</p>
  <div class="vline"></div>

  <h2 class="title script" style="left:742px;top:40px">BOOK YOUR TABLE</h2>
  <div class="rule" style="left:742px;top:100px;width:360px"></div>
  <div class="seal" style="left:742px;top:84px;width:32px;height:32px;border-color:#555"></div>
  <div class="field" style="top:140px"><svg width="16" height="16"><circle cx="8" cy="8" r="8" fill="#ddd"/><rect x="7" y="7" width="2" height="5" fill="#222"/><circle cx="8" cy="4.5" r="1.2" fill="#222"/></svg>Name :</div>
  <div class="field" style="top:187px"><svg width="16" height="12"><rect x=".5" y=".5" width="15" height="11" fill="none" stroke="#ddd"/><path d="M1 1l7 5 7-5" stroke="#ddd" fill="none"/></svg>Email :</div>
  <div class="field" style="top:234px"><svg width="16" height="16" viewBox="0 0 24 24" fill="#ddd"><path d="M6.6 10.8a15 15 0 006.6 6.6l2.2-2.2c.3-.3.7-.4 1-.2 1.1.4 2.3.6 3.6.6.6 0 1 .4 1 1V20c0 .6-.4 1-1 1A17 17 0 013 4c0-.6.4-1 1-1h3.5c.6 0 1 .4 1 1 0 1.3.2 2.5.6 3.6.1.3 0 .7-.2 1z"/></svg>Phone :</div>
  <div class="field" style="top:281px"><svg width="16" height="16"><rect x="1" y="3" width="14" height="12" fill="none" stroke="#ddd" stroke-width="1.5"/><path d="M1 7h14M5 1v4M11 1v4" stroke="#ddd" stroke-width="1.5"/></svg>Date :</div>
  <div class="field" style="top:328px"><svg width="16" height="16"><circle cx="8" cy="8" r="7" fill="none" stroke="#ddd" stroke-width="1.5"/><path d="M8 4v4h3" stroke="#ddd" stroke-width="1.5" fill="none"/></svg>Time :</div>
  <span class="submit">Submit</span>
</section>

<footer class="abs footer wood">
  <div class="col" style="left:100px">
    <h4>QUICK LINKS</h4>
    <ul><li>Home</li><li>Restaurant</li><li>Bar</li><li>Events</li><li>Gallery</li><li>Contact us</li></ul>
  </div>
  <div class="col" style="left:270px">
    <h4>OPENING HOURS</h4>
    <p>Monday - Sunday<br>10:00 am - 11:00 pm</p>
    <h4 style="margin:8px 0 4px">ADDRESS</h4>
    <p>123, Lorem ipsum dolor sit<br>amet, consectetuer,</p>
    <p style="margin-top:4px"><strong>Ph. 123 456 7890</strong></p>
  </div>
  <div class="col" style="left:487px">
    <h4>LOCATION MAP</h4>
    <div class="map" role="img" aria-label="Location map"></div>
  </div>
  <div class="col follow" style="left:747px">
    <h4>FOLLOW US</h4>
    <ul><li><i></i>FRIENDBOOK</li><li><i></i>CHIRPER</li><li><i></i>SNAPGRAM</li><li><i></i>CIRCLES +</li></ul>
  </div>
  <div class="footer-mark">Fizz's Shed<br>and Grill</div>
</footer>

<div class="abs copyright">Copyright © 2016 Fizz's Shed and Grill.All Right Reserved</div>

</body>
</html>
```